Small Business Consulting Firm Needs Letterhead

We need a letterhead for our company "Brightpath Plus". Our company does outbound calling and mailing to business owner's companies who have taken high interest loans. These loans tend to put these businesses in a big financial bind short term, and we help them find better financial options. We would like the design to match our colors of our logo. Headers and footers would look nice, but we are open. We would want it to include our address, website, phone, and email info. Our address - 2000 E. Lamar Blvd. Suite 600Website - www.safeguardtoday.comEmail - info@safeguardtoday.comPhone - 855-726-1938
Industry/Entity Type
Financial Planning
Look and feel
Each slider illustrates characteristics of the customer's brand and the style your logo design should communicate.

```html
<!DOCTYPE html>
<html lang="en">
<head>
<meta charset="utf-8">
<title>Brightpath Plus Letterhead</title>
<link rel="stylesheet" href="https://fonts.googleapis.com/css2?family=Lato:wght@400;700&family=Italianno&display=swap">
<style>
  :root {
    --backdrop: #e9eaeb;
    --paper: #ffffff;
    --ink: #3c3c3c;
    --ink-soft: #6b6b6b;
    --green: #3fae3a;
    --green-deep: #178f4c;
    --green-light: #74c447;
  }
  * { box-sizing: border-box; margin: 0; padding: 0; }
  html, body {
    width: 1200px; height: 795px; overflow: hidden;
    background: var(--backdrop);
  }
  body {
    display: flex; align-items: center; justify-content: center;
    font-family: "Lato", Arial, sans-serif;
    color: var(--ink);
  }
  .letterhead {
    position: relative;
    width: 534px; height: 755px;
    background: var(--paper);
    box-shadow: 0 2px 10px rgba(0,0,0,0.12);
    overflow: hidden;
  }
  .corner-art {
    position: absolute;
    background: linear-gradient(135deg, var(--green-light), var(--green) 55%, var(--green-deep));
  }
  .corner-art--header {
    top: 0; right: 0; width: 260px; height: 110px;
    clip-path: polygon(0 0, 100% 0, 100% 100%);
  }
  .corner-art--footer {
    bottom: 0; left: 0; width: 280px; height: 110px;
    clip-path: polygon(0 0, 100% 100%, 0 100%);
  }
  .brand {
    position: absolute; top: 78px; left: 48px;
    display: flex; align-items: center; gap: 8px;
  }
  .brand-mark { width: 14px; height: 14px; background: var(--green); }
  .brand-name {
    font-size: 17px; font-weight: 400; letter-spacing: 1.5px;
    text-transform: uppercase; color: var(--ink-soft);
  }
  .letter {
    position: absolute; top: 140px; left: 80px; width: 400px;
    font-size: 7.6px; line-height: 1.55; color: var(--ink-soft);
  }
  .letter-date { margin-bottom: 12px; }
  .recipient { margin-bottom: 16px; font-style: normal; }
  .recipient strong { color: var(--ink); font-weight: 700; }
  .salutation { margin-bottom: 10px; }
  .letter-body { margin-bottom: 14px; }
  .closing { margin-top: 22px; }
  .signature {
    font-family: "Italianno", cursive;
    font-size: 30px; color: #222; line-height: 1; margin-top: 2px;
  }
  .contact {
    position: absolute; right: 40px; bottom: 120px;
    list-style: none; font-size: 8px; line-height: 1.7; color: var(--ink-soft);
  }
  .contact li { display: flex; align-items: center; gap: 6px; }
  .contact svg { width: 7px; height: 7px; fill: var(--green); flex: none; }
</style>
</head>
<body>
  <main class="letterhead">
    <div class="corner-art corner-art--header" role="img" aria-label="Green geometric header decoration"></div>

    <header class="brand">
      <span class="brand-mark"></span>
      <span class="brand-name">Brightpath Plus</span>
    </header>

    <section class="letter">
      <div class="letter-date">01 January 2050</div>
      <address class="recipient">
        <strong>Company (Pvt) Ltd.</strong><br>
        PO Box 4821 Elmford St<br>
        Sample City Country 4821
      </address>
      <div class="salutation">Dear Martin Caldwell,</div>
      <p class="letter-body">Lorem ipsum dolor sit amet, consectetuer adipiscing elit, sed diam nonummy nibh euismod tincidunt ut laoreet dolore magna aliquam erat volutpat. Ut wisi enim ad minim veniam, quis nostrud exerci tation ullamcorper suscipit lobortis nisl ut aliquip ex ea commodo consequat. Duis dolore te feugait nulla facilisi. Nam liber tempor cum soluta nobis eleifend option congue nihil imperdiet doming id quod mazim placerat facer possim assum. Lorem ipsum dolor sit amet, consectetuer adipiscing elit, sed diam nonummy nibh euismod tincidunt ut laoreet dolore magna aliquam erat volutpat. Ut wisi enim ad minim veniam, quis nostrud exerci tation ullamcorper suscipit lobortis nisl ut aliquip ex ea commodo consequat.</p>
      <p class="letter-body">Consectetuer adipiscing elit, sed diam nonummy nibh euismod tincidunt ut laoreet dolore magna aliquam erat volutpat. Ut wisi enim ad minim veniam, quis nostrud exerci tation ullamcorper suscipit lobortis nisl ut aliquip ex ea commodo consequat. Consectetuer adipiscing elit, sed diam nonummy nibh euismod tincidunt ut laoreet dolore magna aliquam erat volutpat. Ut wisi enim ad minim veniam, quis nostrud exerci tation ullamcorper suscipit lobortis nisl ut aliquip ex ea commodo consequat.</p>
      <p class="letter-body">Consectetuer adipiscing elit, sed diam nonummy nibh euismod tincidunt ut laoreet dolore magna aliquam erat volutpat. Ut wisi enim ad minim veniam, quis nostrud exerci tation ullamcorper suscipit lobortis nisl ut aliquip ex ea commodo consequat. Consectetuer adipiscing elit, sed diam nonummy nibh euismod tincidunt ut laoreet dolore magna aliquam erat volutpat. Ut wisi enim ad minim veniam, quis nostrud exerci tation ullamcorper suscipit lobortis nisl ut aliquip ex ea commodo consequat.</p>
      <div class="closing">Sincerely Yours</div>
      <div class="signature">Daniel Roy Whitmore</div>
    </section>

    <ul class="contact">
      <li><svg viewBox="0 0 10 10"><path d="M2 0h2l1 3-1.5 1a6 6 0 0 0 2.5 2.5L7 5l3 1v2a2 2 0 0 1-2 2A8 8 0 0 1 0 2a2 2 0 0 1 2-2z"/></svg>855-726-1938</li>
      <li><svg viewBox="0 0 10 10"><path d="M0 2h10v6H0zM1 3v.4l4 2.4 4-2.4V3z"/></svg>info@brightpathplus.com</li>
      <li><svg viewBox="0 0 10 10"><circle cx="5" cy="5" r="5"/></svg>www.brightpathplus.com</li>
      <li><svg viewBox="0 0 10 10"><path d="M5 0a3.5 3.5 0 0 1 3.5 3.5C8.5 6 5 10 5 10S1.5 6 1.5 3.5A3.5 3.5 0 0 1 5 0z"/></svg>4170 W. Corwin Ave. Suite 310</li>
    </ul>

    <div class="corner-art corner-art--footer" role="img" aria-label="Green geometric footer decoration"></div>
  </main>
</body>
</html>
```